Mira Bloom Fitness Coaching Project

I am a personal trainer based in London. My services include one-on-one PT sessions, bootcamps.
I would like the design to be minimalistic. With light colours: white, pink, purple.
I specialise in weight loss, flexibility, mobility.

Tessa Brogan
Personal Trainer
Email: tessa.brogan@quellmail.com
tel: 07700218493
Instagram: Mira Bloom

Target Market(s)

adults, mostly females (age 18-50).

Industry/Entity Type

Fitness

Contact Information for Business Card

Tessa Brogan
Personal Trainer
tel: 07700218493
Instagram: Mira Bloom

Font styles to use
Serif

Colors
eea4c8
fbd4d5
fdf9cf
cfeae6
cee9f5

Requirements
Nice to have
• minimalistic style
• easy to read and remember

```html
<!DOCTYPE html>
<html lang="en">
<head>
<meta charset="utf-8">
<title>Tessa Brogan – Business Card</title>
<link rel="stylesheet" href="https://fonts.googleapis.com/css2?family=Lora:wght@400;600&family=Playfair+Display:wght@600&display=swap">
<style>
  :root {
    --backdrop: #d8d3dc;
    --card-white: #ffffff;
    --pink: #eea4c8;
    --blush: #fbd4d5;
    --cream: #fdf9cf;
    --mint: #cfeae6;
    --sky: #cee9f5;
    --lilac: #c9aedb;
    --lilac-deep: #b395cc;
    --ink: #3f2a48;
    --ink-soft: #7a6482;
  }
  * { margin: 0; padding: 0; box-sizing: border-box; }
  html, body {
    width: 1200px; height: 801px; overflow: hidden;
    background: var(--backdrop);
    font-family: "Lora", serif;
  }
  .canvas { position: relative; width: 1200px; height: 801px; }

  .card {
    position: absolute; top: 170px;
    width: 460px; height: 460px;
    background: var(--card-white);
    overflow: hidden;
    box-shadow: 0 16px 36px rgba(63, 42, 72, 0.25);
  }
  .card--front { left: 90px; }
  .card--back { left: 650px; }

  .photo {
    position: absolute; top: 0; left: 0; height: 100%;
    background: linear-gradient(180deg,
      var(--pink) 0%, var(--blush) 40%,
      var(--mint) 50%, var(--sky) 70%,
      var(--cream) 100%);
  }
  .card--front .photo { width: 50%; }
  .card--back .photo { width: 47%; }

  .name {
    font-family: "Playfair Display", serif;
    font-weight: 600; color: var(--ink);
    line-height: 1.1; white-space: nowrap;
  }
  .title {
    font-family: "Lora", serif;
    font-weight: 400; color: var(--ink-soft);
    white-space: nowrap;
  }

  /* front */
  .front-panel {
    position: absolute; top: 0; left: 50%; width: 50%; height: 100%;
    background: linear-gradient(160deg, var(--lilac) 0%, var(--lilac-deep) 100%);
  }
  .name-label {
    position: absolute; top: 48px; left: 56%; right: 0;
    background: var(--card-white);
    padding: 12px 14px 12px 18px;
  }
  .name-label .name { font-size: 20px; }
  .name-label .title { font-size: 11px; margin-top: 4px; }

  /* back */
  .bands {
    position: absolute; top: 0; left: 51%; width: 24px; height: 100%;
    display: flex; justify-content: space-between;
  }
  .band { width: 8px; height: 100%; background: var(--pink); }
  .back-info {
    position: absolute; top: 58px; left: 63%; right: 10px;
  }
  .back-info .name { font-size: 20px; }
  .back-info .title { font-size: 11px; margin-top: 5px; }
  .contacts { list-style: none; margin-top: 52px; }
  .contact {
    display: flex; align-items: center; gap: 8px;
    font-size: 9.5px; color: var(--ink);
    margin-bottom: 20px; white-space: nowrap;
  }
  .contact svg { width: 10px; height: 10px; flex: none; }
  .square-mark {
    width: 8px; height: 8px; background: var(--ink); flex: none; margin: 0 1px;
  }
</style>
</head>
<body>
<main class="canvas">

  <section class="card card--front" aria-label="Business card front">
    <div class="photo" role="img" aria-label="Photo of a trainer stretching in a wide lunge against a pink and teal wall"></div>
    <div class="front-panel" role="img" aria-label="Soft lilac hexagon pattern"></div>
    <div class="name-label">
      <p class="name">Tessa Brogan</p>
      <p class="title">Personal Trainer</p>
    </div>
  </section>

  <section class="card card--back" aria-label="Business card back">
    <div class="photo" role="img" aria-label="Photo of a trainer stretching in a wide lunge against a pink and teal wall"></div>
    <div class="bands"><span class="band"></span><span class="band"></span></div>
    <div class="back-info">
      <p class="name">Tessa Brogan</p>
      <p class="title">Personal Trainer</p>
      <ul class="contacts">
        <li class="contact">
          <svg viewBox="0 0 12 12" aria-hidden="true"><path d="M3 1l2 2.5-1.2 1.3a7 7 0 0 0 3.4 3.4L8.5 7 11 9l-1.2 2C5.5 11 1 6.5 1 2.2z" fill="#3f2a48"/></svg>
          07700218493
        </li>
        <li class="contact">
          <svg viewBox="0 0 12 12" aria-hidden="true"><rect x="1" y="2.5" width="10" height="7" fill="#3f2a48"/><path d="M1.5 3l4.5 3.5L10.5 3" stroke="#fff" stroke-width="0.9" fill="none"/></svg>
          tessa.brogan@quellmail.com
        </li>
        <li class="contact">
          <span class="square-mark" aria-hidden="true"></span>
          Mira Bloom
        </li>
      </ul>
    </div>
  </section>

</main>
</body>
</html>
```